Event flyer for Sunday night Youth Group

Need a 4 x 6 or 5 x 7 flyer for a new youth group starting on April 14. The youth group is for students in middle school and high school so it needs to look fun and cool, but not childish. I prefer it not to include pictures of people unless it's so obscure you can't really see their faces. I've uploaded some pictures of flyers I like. I've also attached a couple versions of our logo to use on the flyer.
Information the flyer needs to include:
Youth Group
Sundays, 6-8pm (beginning April 14)
Location: Marlowe's - 4219 Quarry Fern Ave N, Keizer, 97318
There will be dinner, games, friends, and a message.
Target Market(s)
Youth ages 13-18
Industry/Entity Type
Church
Font styles to use
Colors
Designer to choose colors to be used in the design.
Look and feel

```html
<!DOCTYPE html>
<html lang="en">
<head>
<meta charset="utf-8">
<title>Youth Group Sunday Flyer</title>
<link rel="stylesheet" href="https://fonts.googleapis.com/css2?family=Yellowtail&family=Bebas+Neue&family=Nunito:wght@700;800;900&display=swap">
<style>
  :root {
    --ink: #050505;
    --night: #0b0906;
    --olive: #6d6a1f;
    --amber: #8a5a1c;
    --ember: #5a2414;
    --gold-top: #fff6c8;
    --gold: #ffdf00;
    --badge-a: #e8452a;
    --badge-b: #f26a24;
    --band: #d9973f;
    --white: #ffffff;
  }
  * { margin: 0; padding: 0; box-sizing: border-box; }
  html, body { width: 857px; height: 1200px; overflow: hidden; background: var(--ink); }
  .flyer {
    position: relative;
    width: 857px;
    height: 1200px;
    overflow: hidden;
    font-family: "Nunito", sans-serif;
    color: var(--white);
  }
  .backdrop {
    position: absolute;
    inset: 0;
    background:
      radial-gradient(ellipse 60% 30% at 55% 62%, rgba(190,180,70,.55), transparent 70%),
      radial-gradient(ellipse 45% 35% at 80% 55%, rgba(200,190,110,.35), transparent 70%),
      radial-gradient(ellipse 40% 30% at 15% 60%, rgba(150,60,40,.45), transparent 70%),
      linear-gradient(180deg, var(--night) 0%, var(--night) 18%, #2a2010 35%, var(--olive) 58%, var(--amber) 75%, var(--ember) 92%, var(--ink) 100%);
  }
  .brand {
    position: absolute;
    left: 620px;
    top: 60px;
    width: 200px;
    text-align: center;
    font-weight: 800;
    color: var(--white);
    letter-spacing: 1px;
  }
  .brand-mark {
    display: block;
    width: 40px;
    height: 40px;
    margin: 0 auto 40px;
    background: var(--white);
  }
  .brand-name { font-size: 22px; line-height: 1; }
  .brand-sub { font-size: 11px; letter-spacing: 5px; margin-top: 6px; }

  .title-art {
    position: absolute;
    left: 0;
    top: 0;
    width: 857px;
    height: 1200px;
    overflow: hidden;
    pointer-events: none;
  }
  .title-word {
    font-family: "Yellowtail", "Brush Script MT", cursive;
    font-weight: 400;
  }
  .title-shadow { fill: var(--ink); }

  .day-badge {
    position: absolute;
    left: 443px;
    top: 647px;
    width: 207px;
    height: 80px;
    border-radius: 6px;
    background: linear-gradient(90deg, var(--badge-a), var(--badge-b) 60%, var(--badge-a));
    font-family: "Bebas Neue", sans-serif;
    font-size: 92px;
    line-height: 88px;
    text-align: center;
    color: var(--white);
    overflow: hidden;
  }

  .icon { position: absolute; }
  .icon-calendar { left: 57px; top: 857px; width: 95px; height: 95px; }
  .icon-map { left: 525px; top: 857px; width: 87px; height: 87px; }

  .date {
    position: absolute;
    left: 57px;
    top: 958px;
    width: 140px;
    height: 68px;
    font-weight: 900;
    line-height: 1;
  }
  .date-day { position: absolute; left: 0; top: 0; font-size: 54px; letter-spacing: -2px; }
  .date-suffix { position: absolute; left: 54px; top: -2px; font-size: 30px; }
  .date-month { position: absolute; left: 53px; top: 38px; font-size: 28px; font-weight: 800; }
  .time {
    position: absolute;
    left: 57px;
    top: 1029px;
    width: 137px;
    height: 41px;
    background: var(--white);
    color: var(--ink);
    font-weight: 900;
    font-size: 30px;
    line-height: 41px;
    text-align: center;
  }
  .address {
    position: absolute;
    left: 523px;
    top: 958px;
    font-style: normal;
    font-weight: 800;
    font-size: 32px;
    line-height: 40px;
    white-space: nowrap;
  }
  .band {
    position: absolute;
    left: 0;
    top: 1111px;
    width: 857px;
    height: 46px;
    background: var(--band);
    color: var(--ink);
    font-weight: 900;
    font-size: 24px;
    letter-spacing: 1.2px;
    line-height: 46px;
    text-align: center;
    white-space: nowrap;
  }
</style>
</head>
<body>
<main class="flyer">
  <div class="backdrop" role="img" aria-label="Warm bokeh lights over a silhouetted concert crowd with raised hands"></div>

  <div class="brand">
    <span class="brand-mark"></span>
    <div class="brand-name">WAYSIDE</div>
    <div class="brand-sub">FELLOWSHIP</div>
  </div>

  <svg class="title-art" viewBox="0 0 857 1200" role="img" aria-label="Youth Group">
    <defs>
      <linearGradient id="gold-youth" gradientUnits="userSpaceOnUse" x1="0" y1="160" x2="0" y2="420">
        <stop offset="0" stop-color="#fff6c8"/>
        <stop offset="0.6" stop-color="#ffdf00"/>
        <stop offset="1" stop-color="#ffdf00"/>
      </linearGradient>
      <linearGradient id="gold-group" gradientUnits="userSpaceOnUse" x1="0" y1="435" x2="0" y2="650">
        <stop offset="0" stop-color="#fff6c8"/>
        <stop offset="0.6" stop-color="#ffdf00"/>
        <stop offset="1" stop-color="#ffdf00"/>
      </linearGradient>
    </defs>
    <text class="title-word title-shadow" x="74" y="416" font-size="330" textLength="640" lengthAdjust="spacingAndGlyphs">Youth</text>
    <text class="title-word" x="69" y="411" font-size="330" textLength="640" lengthAdjust="spacingAndGlyphs" fill="url(#gold-youth)">Youth</text>
    <text class="title-word title-shadow" x="316" y="645" font-size="290" textLength="490" lengthAdjust="spacingAndGlyphs">Group</text>
    <text class="title-word" x="311" y="640" font-size="290" textLength="490" lengthAdjust="spacingAndGlyphs" fill="url(#gold-group)">Group</text>
  </svg>

  <div class="day-badge">SUNDAY</div>

  <svg class="icon icon-calendar" viewBox="0 0 95 95" fill="none" stroke="#fff" stroke-width="3.5" stroke-linejoin="round">
    <rect x="2" y="10" width="80" height="72" rx="5"/>
    <line x1="2" y1="24" x2="82" y2="24"/>
    <g stroke-linecap="round">
      <line x1="14" y1="3" x2="14" y2="16"/><line x1="32" y1="3" x2="32" y2="16"/>
      <line x1="50" y1="3" x2="50" y2="16"/><line x1="68" y1="3" x2="68" y2="16"/>
    </g>
    <g stroke-width="3">
      <rect x="11" y="32" width="9" height="9"/><rect x="26" y="32" width="9" height="9"/><rect x="41" y="32" width="9" height="9"/><rect x="56" y="32" width="9" height="9"/>
      <rect x="11" y="48" width="9" height="9"/><rect x="26" y="48" width="9" height="9"/><rect x="41" y="48" width="9" height="9"/>
      <rect x="11" y="64" width="9" height="9"/><rect x="26" y="64" width="9" height="9"/><rect x="41" y="64" width="9" height="9"/>
    </g>
    <circle cx="76" cy="76" r="17" fill="#3a2a10"/>
    <polyline points="76,66 76,77 70,82" stroke-linecap="round"/>
  </svg>

  <svg class="icon icon-map" viewBox="0 0 87 87" fill="none" stroke="#fff" stroke-width="3.5" stroke-linejoin="round" stroke-linecap="round">
    <path d="M52 2 H6 a4 4 0 0 0 -4 4 V80 a4 4 0 0 0 4 4 H80 a4 4 0 0 0 4 -4 V48"/>
    <line x1="2" y1="84" x2="46" y2="40"/>
    <line x1="4" y1="4" x2="70" y2="84"/>
    <path d="M68 62 L56 36 a14 14 0 1 1 24 0 Z"/>
    <circle cx="68" cy="27" r="5"/>
  </svg>

  <div class="date">
    <span class="date-day">14</span>
    <span class="date-suffix">th</span>
    <span class="date-month">APRIL</span>
  </div>
  <div class="time">6–8pm</div>

  <address class="address">
    Marlowe's – 4219<br>
    Quarry Fern Ave N<br>
    Keizer, 97318
  </address>

  <div class="band">There will be Dinner, Games, Friends, &amp; a Message</div>
</main>
</body>
</html>
```